NZ First of it's kind solutions directory and marketplace for busy Mums needs a business card design

We need a business card design for our new nationwide business in NZ (long term plans to go global). We provide solutions to the everyday challenges that busy Mums face by connecting them with quality communities and suppliers of carefully selected, relevant products and services. We sell direct via our online marketplace. The final design should communicate our values of inclusivity, quality and smart solutions. Colours should incorporate our logo colour palette of #477077 and #6ba8b2. Our website is at https://www.brightnestmums.example

Target Market(s)

busy Mums, Age 28 – 50, female, income over $100K, location main centres NZ primarily but NZ wide. Is likely juggling work or career with a young family. Probably had hobbies which have fallen by the wayside.
-Wants to succeed in her chosen career without compromising on family life
-to successfully juggle her career without feeling like she is compromising her children
- Is time poor, something always has to give and it’s generally her health (she’ll stay up late, get stressed)
- probably ex corporate or professional career. Has discretional income

Industry/Entity Type

Business

Contact Information for Business Card

Lena Forbisher, Founder, BrightNestMums.example (Strapline Tap; Gather; Sorted), 47 Kowhai Terrace, Ellerslie, Auckland 1051, New Zealand. Mob: 021 483 517 Ph: +64 (0)9 571 4860

Font styles to use
Other font styles liked:
• Raleway, and/or Architects Daughter

Colors
00a990
33b8a4
86cfc6
cfeae6

Requirements
Must have
• the above details, streamline. the logo and colours associated with those logos
Should not have
• foil or metallic colours

```html
<!DOCTYPE html>
<html lang="en">
<head>
<meta charset="utf-8">
<title>BrightNestMums – Business Card</title>
<link rel="stylesheet" href="https://fonts.googleapis.com/css2?family=Roboto:wght@400;700&family=Roboto+Condensed:wght@700&display=swap">
<style>
  :root {
    --backdrop: #2a2a2a;
    --card-front: #f1f1f1;
    --card-back: #86cfc6;
    --brand-dark: #477077;
    --brand-light: #6ba8b2;
    --text: #555a5c;
    --faint: #e2e4e4;
  }
  * { box-sizing: border-box; margin: 0; padding: 0; }
  html, body { width: 1200px; height: 960px; overflow: hidden; }
  body {
    background: var(--backdrop);
    position: relative;
    font-family: "Roboto", Arial, sans-serif;
    color: var(--text);
  }
  .card {
    position: absolute;
    width: 600px;
    height: 343px;
    border-radius: 20px;
    overflow: hidden;
  }
  .card--front { left: 314px; top: 113px; background: var(--card-front); }
  .card--back { left: 311px; top: 472px; background: var(--card-back); }

  .brand {
    position: absolute;
    display: flex;
    align-items: center;
  }
  .brand__dot { border-radius: 50%; background: var(--brand-dark); flex: none; }
  .brand__name { font-weight: 700; color: var(--brand-dark); letter-spacing: -0.5px; line-height: 1; }

  .card--front .brand { left: 48px; top: 68px; gap: 12px; }
  .card--front .brand__dot { width: 32px; height: 32px; }
  .card--front .brand__name { font-size: 31px; }

  .backdrop-disc {
    position: absolute;
    left: 382px; top: 90px;
    width: 176px; height: 176px;
    border-radius: 50%;
    background: var(--faint);
  }

  .contact {
    position: absolute;
    left: 56px;
    list-style: none;
    font-size: 14.5px;
    line-height: 18px;
  }
  .contact--address { top: 171px; }
  .contact--lines { top: 238px; }
  .contact li { display: flex; align-items: flex-start; gap: 13px; }
  .contact svg { width: 15px; height: 15px; flex: none; margin-top: 2px; fill: var(--brand-dark); }

  .person {
    position: absolute;
    right: 50px; top: 211px;
    text-align: right;
  }
  .person__name {
    font-family: "Roboto Condensed", "Arial Narrow", sans-serif;
    font-weight: 700;
    font-size: 21px;
    color: var(--brand-dark);
    line-height: 24px;
  }
  .person__role {
    font-size: 15px;
    color: var(--brand-light);
    letter-spacing: 0.5px;
    line-height: 20px;
  }
  .edge-tab {
    position: absolute;
    right: 0; top: 213px;
    width: 15px; height: 40px;
    background: var(--brand-dark);
  }

  .card--back .brand { left: 130px; top: 146px; gap: 14px; }
  .card--back .brand__dot { width: 40px; height: 40px; }
  .card--back .brand__name { font-size: 41px; }
  .strapline {
    position: absolute;
    left: 0; right: 0; top: 286px;
    text-align: center;
    font-size: 14.5px;
    color: var(--text);
  }
</style>
</head>
<body>
  <section class="card card--front" aria-label="Card front">
    <div class="backdrop-disc" aria-hidden="true"></div>
    <div class="brand">
      <span class="brand__dot" aria-hidden="true"></span>
      <span class="brand__name">BrightNestMums</span>
    </div>

    <ul class="contact contact--address">
      <li>
        <svg viewBox="0 0 16 16" aria-hidden="true"><path d="M8 1a5 5 0 0 0-5 5c0 3.6 5 9 5 9s5-5.4 5-9a5 5 0 0 0-5-5zm0 7a2 2 0 1 1 0-4 2 2 0 0 1 0 4z"/></svg>
        <span>47 Kowhai Terrace<br>Ellerslie, Auckland 1051<br>New Zealand.</span>
      </li>
    </ul>

    <ul class="contact contact--lines">
      <li>
        <svg viewBox="0 0 16 16" aria-hidden="true"><path d="M3.6 1.5l2.2 2.6-1.3 1.6a9 9 0 0 0 5.8 5.8l1.6-1.3 2.6 2.2-1.4 2A11.5 11.5 0 0 1 1.5 2.9z"/></svg>
        <span>+64 (0)9 571 4860</span>
      </li>
      <li>
        <svg viewBox="0 0 16 16" aria-hidden="true"><path d="M4.5 1h7v14h-7zM6 2.5v9.5h4V2.5zM7.3 13h1.4v1H7.3z"/></svg>
        <span>021 483 517</span>
      </li>
      <li>
        <svg viewBox="0 0 16 16" aria-hidden="true"><path d="M8 1a7 7 0 1 0 0 14A7 7 0 0 0 8 1zm-1 2.3c-.6.6-1.9 1.1-1.9 2.2 0 1 1.5.9 1.9 1.7.4.8-.3 1.6.4 2.3.7.6 1.4-.3 1.8.8.3 1 .1 2.3.1 2.3A5 5 0 0 1 3 8c0-2 1.6-4.2 4-4.7zm3.1.6A5 5 0 0 1 13 8c-.6 0-1.4-.6-1.6-1.3-.3-.9.4-1.4-.4-2-.5-.3-1.2-.3-1.2-.8z"/></svg>
        <span>BrightNestMums.example</span>
      </li>
    </ul>

    <div class="person">
      <p class="person__name">LENA FORBISHER</p>
      <p class="person__role">FOUNDER</p>
    </div>
    <div class="edge-tab" aria-hidden="true"></div>
  </section>

  <section class="card card--back" aria-label="Card back">
    <div class="brand">
      <span class="brand__dot" aria-hidden="true"></span>
      <span class="brand__name">BrightNestMums</span>
    </div>
    <p class="strapline">Tap; Gather; Sorted</p>
  </section>
</body>
</html>
```